Either a trifold or double sided flyer/brochure

A flyer to help spark interest in a historic preservation project in Peterborough, NH--looking for something that captures the early 19th century rural village and mill times--American Primitive, Shaker, Cross Stitch Sampler...must be able to highlight home history as well as have all owners of house on a single page. Word document attached--can also provide files for the house painting, color photos, borrell photo, advertising photo or part of original settler map.
I like this brochure
http://tessavornick.com/wordpress/dell-lodge-museum-brochure/
community stakeholders, residents,
Historic Preservation, House Museums.

```html
<!DOCTYPE html>
<html lang="en">
<head>
<meta charset="utf-8">
<title>The Ashcombe Homestead — History c. 1826</title>
<link href="https://fonts.googleapis.com/css2?family=Oswald:wght@500;600&family=Old+Standard+TT:wght@400;700&display=swap" rel="stylesheet">
<style>
:root{
  --backdrop:#ebebeb;
  --paper-light:#efe5cf;
  --paper-mid:#e0cfae;
  --paper-edge:#b08656;
  --title-brown:#5a1a0a;
  --ink-dark:#22160f;
  --ink-body:#3a2a1e;
  --maroon:#4e190b;
  --accent-red:#7a2410;
  --sepia-light:#b39770;
  --sepia-mid:#86694a;
  --sepia-dark:#4b3522;
  --tear-white:#f8f6f1;
}
*{box-sizing:border-box;margin:0;padding:0}
html,body{width:1200px;height:2400px;overflow:hidden;background:var(--backdrop)}
body{position:relative;font-family:"Old Standard TT",Georgia,serif;color:var(--ink-body)}

.spread{
  position:absolute;left:40px;width:1120px;height:866px;overflow:hidden;
  background:
    radial-gradient(ellipse at 50% 45%, var(--paper-light) 0%, var(--paper-mid) 62%, var(--paper-edge) 100%);
  box-shadow:0 10px 30px rgba(0,0,0,.18);
}
.spread--cover{top:270px}
.spread--story{top:1256px}

.panel{position:absolute;top:0;height:866px;overflow:hidden}
.panel--left{left:0;width:369px;background:radial-gradient(ellipse at 40% 40%,rgba(245,237,220,.7),rgba(176,134,86,.25) 90%)}
.panel--mid{left:369px;width:371px}
.panel--right{left:740px;width:380px}

.photo{position:absolute}
.photo svg{display:block}

.owners-title{
  position:absolute;left:20px;top:34px;width:320px;
  font-size:17.5px;line-height:24px;letter-spacing:.6px;text-transform:uppercase;color:var(--title-brown);font-weight:400;
}
.rule-accent{position:absolute;left:20px;top:117px;width:46px;height:4px;border-radius:2px;background:var(--accent-red)}
.rule-thin{position:absolute;left:20px;top:118px;width:312px;height:1px;background:rgba(90,26,10,.25)}
.owners-list{position:absolute;left:20px;top:146px;width:324px;list-style:none}
.owner{display:flex;justify-content:space-between;align-items:flex-end;margin-bottom:13px;font-size:12.4px;line-height:15.5px;color:var(--ink-dark)}
.owner__name{width:200px}
.owner__years{white-space:nowrap}

.faded-photo{position:absolute;left:0;bottom:0;width:369px;height:200px;
  background:linear-gradient(180deg,rgba(224,207,174,1) 0%,rgba(134,105,74,.85) 35%,var(--sepia-dark) 100%)}

.circle-photo{position:absolute;border-radius:50%;border:4px solid var(--tear-white);box-shadow:0 2px 6px rgba(0,0,0,.3)}
.circle-photo--house{left:463px;top:264px;width:200px;height:200px;background:linear-gradient(135deg,#3f6fb0 0%,#6a93c7 35%,#d8b54c 36%,#c59c34 100%)}
.circle-photo--latch{left:406px;top:230px;width:200px;height:200px;background:linear-gradient(90deg,#3d5148 0%,#6c8a7c 45%,#8a5a3c 55%,#4a5f55 100%)}
.circle-photo--stair{left:757px;top:351px;width:176px;height:176px;background:linear-gradient(160deg,#e4e0d8 0%,#8a6a4a 55%,#3b2416 100%)}

.ad-box{position:absolute;left:822px;top:382px;width:240px;height:133px;background:#f3efe6;border:2px solid var(--ink-dark);outline:1px solid var(--ink-dark);outline-offset:-6px}
.map-box{position:absolute;left:428px;top:528px;width:260px;height:235px;border:3px solid var(--ink-dark);background:linear-gradient(160deg,#d9dde0 0%,#b9c2c8 60%,#9ea8b0 100%)}

.cover-title{position:absolute;left:740px;top:536px;width:380px;text-align:center;font-family:"Oswald",Impact,sans-serif;font-weight:600;text-transform:uppercase;line-height:56px}
.cover-title__line{display:block;font-size:49px;color:var(--title-brown);letter-spacing:-.5px}
.cover-title__line--dark{color:var(--ink-dark);font-weight:500;font-size:49px}
.cover-rule{position:absolute;left:913px;top:712px;width:44px;height:4px;border-radius:2px;background:var(--accent-red)}
.cover-rule-thin{position:absolute;left:777px;top:713px;width:316px;height:1px;background:rgba(90,26,10,.3)}
.place-badge{position:absolute;left:779px;top:730px;width:312px;height:60px;border-radius:8px;background:var(--maroon);color:var(--paper-light);text-align:center;font-size:22px;line-height:24px;padding-top:7px}

.group-link{position:absolute;display:flex;align-items:center;gap:8px;font-size:16px;color:var(--ink-dark)}
.group-link__mark{width:15px;height:15px;border-radius:3px;background:var(--ink-dark)}

.story-title{position:absolute;left:34px;top:34px;font-family:"Oswald",Impact,sans-serif;font-weight:500;font-size:23.5px;line-height:30px;text-transform:uppercase;color:var(--title-brown);letter-spacing:-.2px}
.story-title__line{display:block}
.story-title__line--dark{color:var(--ink-dark)}
.story-text{position:absolute;font-size:11.4px;line-height:14.6px;text-align:justify;color:var(--ink-body)}
.story-text p{margin-bottom:14px}
.story-text--left{left:34px;top:148px;width:306px}
.story-text--mid{left:24px;top:446px;width:324px}

.snow-photo{position:absolute;left:30px;top:624px;width:306px;height:140px;background:linear-gradient(180deg,#7a7168 0%,#c9a640 45%,#e9e7e2 75%,#f6f5f2 100%);box-shadow:0 1px 3px rgba(0,0,0,.25)}
.side-title{position:absolute;left:30px;top:540px;font-family:"Oswald",Impact,sans-serif;font-weight:500;font-size:21.5px;line-height:29px;text-transform:uppercase;color:var(--title-brown)}
.side-title__line{display:block}
.side-title__line--dark{color:var(--ink-dark)}
.winter-photo{position:absolute;left:0;bottom:0;width:380px;height:235px;background:linear-gradient(180deg,rgba(224,207,174,0) 0%,rgba(160,136,108,.7) 35%,rgba(120,98,74,.85) 100%)}
</style>
</head>
<body>

<!-- Cover spread -->
<section class="spread spread--cover">
  <div class="panel panel--left">
    <h2 class="owners-title">Owners of 57 Elm Hollow Road Peterborough, New Hampshire</h2>
    <div class="rule-thin"></div>
    <div class="rule-accent"></div>
    <ul class="owners-list">
      <li class="owner"><span class="owner__name">Robert Hale (grandson of John Hale) owned the land</span><span class="owner__years">1826</span></li>
      <li class="owner"><span class="owner__name">George S. Ashcombe and Jane (Porter) Ashcombe</span><span class="owner__years">1826–1828</span></li>
      <li class="owner"><span class="owner__name">Deacon Thomas Ward and Alice (Brooks) Ward (Baptist)</span><span class="owner__years">1828–1839</span></li>
      <li class="owner"><span class="owner__name">Elijah Brown Lindell and Achsah (Rowe) Lindell (mortgage between Samuel Brooks and Lindell is 1845)</span><span class="owner__years">1839–1877</span></li>
      <li class="owner"><span class="owner__name">Mary Ellen Lindell</span><span class="owner__years">1877–1898</span></li>
      <li class="owner"><span class="owner__name">James Carver</span><span class="owner__years">1898–1904</span></li>
      <li class="owner"><span class="owner__name">Fred Parker Borrell and Grace E. (Talbot) Borrell</span><span class="owner__years">1904–1956</span></li>
      <li class="owner"><span class="owner__name">Elinor (Borrell) Whitcomb and Frank O Whitcomb (Elinor was born in house on July 29, 1911)</span><span class="owner__years">1955–1998</span></li>
      <li class="owner" style="align-items:flex-start"><span class="owner__name">James H. Osterhout and Maria Ortega Osterhout (James was nephew of Elinor (Borrell) Whitcomb)</span><span class="owner__years">1998–2015</span></li>
      <li class="owner"><span class="owner__name">Brookhaven</span><span class="owner__years">2015–2022</span></li>
      <li class="owner"><span class="owner__name">Edward M. Pellham and Albert A. Treadwell, Jr.</span><span class="owner__years">2022</span></li>
    </ul>
    <div class="faded-photo" role="img" aria-label="Old sepia photograph of the farmhouse and barn"></div>
  </div>

  <div class="photo" style="left:369px;top:0" role="img" aria-label="Sepia photograph of the homestead among tall trees">
    <svg width="751" height="420" viewBox="0 0 751 420">
      <defs>
        <linearGradient id="coverSepia" x1="0" y1="0" x2="0" y2="1">
          <stop offset="0" stop-color="#5a4128"/>
          <stop offset=".45" stop-color="#9a7c55"/>
          <stop offset="1" stop-color="#6e5236"/>
        </linearGradient>
      </defs>
      <polygon fill="url(#coverSepia)" points="0,0 751,0 751,400 710,398 680,387 640,388 610,380 570,378 540,368 500,371 470,360 430,361 400,351 360,352 330,340 290,342 260,330 225,333 190,312 160,322 125,306 95,314 60,301 30,308 0,300"/>
      <polygon fill="var(--tear-white)" points="0,300 30,308 60,301 95,314 125,306 160,322 190,312 225,333 260,330 290,342 330,340 360,352 400,351 430,361 470,360 500,371 540,368 570,378 610,380 640,388 680,387 710,398 751,400 751,412 720,408 690,414 650,402 615,395 580,392 545,384 505,386 470,374 435,377 400,364 362,367 328,354 292,356 258,344 222,347 188,330 155,336 122,320 92,328 58,314 28,320 0,312"/>
    </svg>
  </div>
  <div class="circle-photo circle-photo--house" role="img" aria-label="Yellow clapboard gable of the house in winter light"></div>
  <div class="ad-box" role="img" aria-label="Period newspaper advertisement for a wool carder and cloth dresser"></div>
  <div class="map-box" role="img" aria-label="Section of the original settler lot map"></div>

  <h1 class="cover-title">
    <span class="cover-title__line">The Ashcombe</span>
    <span class="cover-title__line">Homestead</span>
    <span class="cover-title__line cover-title__line--dark">History c. 1826</span>
  </h1>
  <div class="cover-rule-thin"></div>
  <div class="cover-rule"></div>
  <div class="place-badge">Peterborough,<br>New Hampshire</div>

  <div class="group-link" style="left:444px;top:819px"><span class="group-link__mark"></span>join their Community Group</div>
  <div class="group-link" style="left:813px;top:819px"><span class="group-link__mark"></span>join their Community Group</div>
</section>

<!-- Story spread -->
<section class="spread spread--story">
  <div class="panel panel--left">
    <h2 class="story-title">
      <span class="story-title__line">The Ashcombe Homestead</span>
      <span class="story-title__line">History c. 1826</span>
      <span class="story-title__line story-title__line--dark">Peterborough, New Hampshire</span>
    </h2>
    <div class="story-text story-text--left">
      <p>In 1826, George S. Ashcombe and his wife, Jane (Porter) Ashcombe purchased 26 acres from Robert Hale on the Contoocook River, north of Thayer's Woolen Mill in South Peterborough, NH. This parcel was carved out lot #32 which was comprised of 268 acres that were deeded to John Hale (Robert Hale's grandfather) by Jeremiah Lovell and John Mercer on May 5, 1762. It is believed that Ashcombe, who was blacksmith, built the house that currently stands at 57 Elm Hollow Road in Peterborough, NH. He also built his forge on the site down by the river. It is likely that much of the forged hardware in the home was crafted by him. Feeling the need to leave Peterborough for a new frontier, Ashcombe left town with his brother, Baxter, to purchase land in the emerging communities of Orleans County, NY. Before doing so, Ashcombe sold the home, shop and buildings to Thomas Ward and his wife Alice (Brooks) Ward in 1828.</p>
      <p>By trade, Thomas Ward was a cloth dresser and wool-carder. He was also a deeply religious man and served as deacon in the emerging, but still quite small, Baptist community. In those days, small groups of the Baptists and Methodists met in the Carleton Home for bible study, prayers and singing. The Carletons were well known abolitionists and their house served as a stop on the Underground Railroad. Deacon Ward died in 1839 and his estate was managed by Samuel Brooks—very likely a relative of Alice—who protected Alice's dower. The property was then sold to Elijah Brown Lindell and his wife Achsah (Rowe) Lindell.</p>
    </div>
    <div class="snow-photo" role="img" aria-label="Painting of the yellow house and barn in snow"></div>
  </div>

  <div class="panel panel--mid">
    <div class="photo" style="left:0;top:0" role="img" aria-label="Sepia portrait photograph of a woman standing by the house">
      <svg width="371" height="400" viewBox="0 0 371 400">
        <defs>
          <linearGradient id="portraitSepia" x1="0" y1="0" x2="0" y2="1">
            <stop offset="0" stop-color="#6e5a44"/>
            <stop offset=".5" stop-color="#a48d6e"/>
            <stop offset="1" stop-color="#8a7458"/>
          </linearGradient>
        </defs>
        <polygon fill="url(#portraitSepia)" points="0,0 371,0 371,372 340,366 310,368 280,355 250,358 220,345 190,348 160,336 130,338 100,326 70,328 40,318 0,310"/>
        <polygon fill="var(--tear-white)" points="0,310 40,318 70,328 100,326 130,338 160,336 190,348 220,345 250,358 280,355 310,368 340,366 371,372 371,384 342,379 308,381 278,368 248,371 218,358 188,361 158,349 128,351 98,339 68,341 38,330 0,322"/>
      </svg>
    </div>
    <div class="story-text story-text--mid">
      <p>Elijah was quite industrious and continued to expand the wool mill. He was an early investor in the Ridgeline Railroad and ceded a right of way to the railroad on the homestead. The mill eventually came under the control of his son, Henry A. Lindell, and operated until it burned down on April 20, 1874. Elijah passed away in 1877 and left the home to Mary Ellen Lindell who was most commonly known as “Ellen.”</p>
      <p>Ellen Lindell was approached in 1891 by Allie Thayer, the owner of the Thayer's Mill Complex, to ask if she would be willing to rent out the home to a couple from Boston. This turned out to be Marian and Edward Hartwell, the founders of the Hartwell Colony, who ended up spending their first summer in Peterborough, NH in the home. Marian recalls in her writings: “You can't fail to remember the two-story farmhouse almost across the road from the iron bridge, now occupied by the Borrell Family. It had never been painted and was a lovely soft gray in color. There were really only four rooms and a kitchen, spotlessly clean and adequately furnished, which really didn't mean much but some chairs, tables and beds. Then in the kitchen was something that fascinated me, a stone bowl into which the clearest of water was all the time pouring and then running off into a a drain....”</p>
    </div>
  </div>

  <div class="panel panel--right">
    <div class="winter-photo" role="img" aria-label="Faded sepia photograph of the farmhouse in winter"></div>
    <div class="photo" style="left:0;top:0" role="img" aria-label="Sepia photograph of an elderly couple seated before flowers">
      <svg width="380" height="440" viewBox="0 0 380 440">
        <defs>
          <linearGradient id="coupleSepia" x1="0" y1="0" x2="0" y2="1">
            <stop offset="0" stop-color="#b7a58c"/>
            <stop offset=".4" stop-color="#6b5744"/>
            <stop offset="1" stop-color="#3e2f22"/>
          </linearGradient>
        </defs>
        <polygon fill="url(#coupleSepia)" points="0,0 380,0 380,352 350,360 320,356 290,370 260,366 230,380 200,376 170,390 140,386 110,400 80,396 50,410 20,406 0,416"/>
        <polygon fill="var(--tear-white)" points="0,416 20,406 50,410 80,396 110,400 140,386 170,390 200,376 230,380 260,366 290,370 320,356 350,360 380,352 380,364 352,373 322,368 292,382 262,378 232,392 202,388 172,402 142,398 112,412 82,408 52,422 22,418 0,428"/>
      </svg>
    </div>
    <h2 class="side-title">
      <span class="side-title__line">The Ashcombe Homestead</span>
      <span class="side-title__line">History c. 1826</span>
      <span class="side-title__line side-title__line--dark">Peterborough, New Hampshire</span>
    </h2>
  </div>

  <div class="circle-photo circle-photo--latch" role="img" aria-label="Hand-forged iron door latch on weathered green paint"></div>
  <div class="circle-photo circle-photo--stair" role="img" aria-label="Narrow wooden staircase inside the house"></div>

  <div class="group-link" style="left:30px;top:818px"><span class="group-link__mark"></span>join their Community Group</div>
  <div class="group-link" style="left:775px;top:818px"><span class="group-link__mark"></span>join their Community Group</div>
</section>

</body>
</html>
```